RWT Fittings Ltd Business Cards

We need a business card with our business logo. We provide window and door installations on high-rises in west coast British Colombia, Canada.

I would like my business information and details on one side of the card, and the other side the company name with logo

Target Market(s)

General Contractors

Industry/Entity Type

Construction

Contact Information for Business Card

one side i want my company name and logo in the dark theme logo that i provided

Requirements
Must have
• Marco Peltieri, 16045518293, RWTFittings@mailbox-demo.com, 1407-5194 Linden Row Burnaby BC, V5H 2K9, Owner & Manager

```html
<!DOCTYPE html>
<html lang="en">
<head>
<meta charset="utf-8">
<title>RWT Fittings Ltd — Business Cards</title>
<link rel="stylesheet" href="https://fonts.googleapis.com/css2?family=Montserrat:wght@700;800&family=Poppins:wght@300;400;500&display=swap">
<style>
  :root{
    --backdrop:#d3d3cf;
    --card-white:#ffffff;
    --card-dark:#2b2b2c;
    --brand-blue:#29a3de;
    --ink-grey:#5c5c5c;
  }
  *{box-sizing:border-box;margin:0;padding:0}
  html,body{width:1200px;height:801px;overflow:hidden}
  body{background:var(--backdrop);font-family:"Poppins",sans-serif;position:relative}

  .card{position:absolute;width:540px;height:309px;border-bottom:5px solid var(--brand-blue);box-shadow:0 14px 30px rgba(0,0,0,.18)}
  .card--front{left:48px;top:246px;background:var(--card-white)}
  .card--back{left:612px;top:246px;background:var(--card-dark)}

  .brand{position:absolute;left:34px;top:128px;display:flex;align-items:center;gap:9px;white-space:nowrap}
  .brand__square{width:20px;height:20px;background:var(--brand-blue);flex:none}
  .brand__name{font-family:"Poppins",sans-serif;font-weight:500;font-size:21px;color:var(--brand-blue);letter-spacing:.3px;line-height:1}

  .divider{position:absolute;left:262px;top:86px;width:2px;height:112px;background:var(--brand-blue)}

  .person{position:absolute;left:282px;top:84px}
  .person__name{font-family:"Montserrat",sans-serif;font-weight:800;font-size:22px;color:var(--brand-blue);letter-spacing:.5px;line-height:1.05;white-space:nowrap}
  .person__title{font-weight:300;font-size:13px;color:var(--ink-grey);margin-top:2px}

  .contact{position:absolute;left:282px;top:146px;list-style:none}
  .contact__item{display:flex;align-items:center;gap:7px;font-weight:300;font-size:12px;color:var(--ink-grey);line-height:17px;white-space:nowrap}
  .contact__item svg{width:10px;height:10px;flex:none}

  .address{position:absolute;left:34px;top:256px;display:flex;align-items:center;gap:8px;font-weight:300;font-size:13px;color:var(--ink-grey);white-space:nowrap}
  .address svg{width:11px;height:13px}

  .back-pattern{position:absolute;inset:0;background:linear-gradient(135deg,#141414 0%,#2b2b2c 45%,#4a4a4b 100%)}
  .back-brand{position:absolute;right:36px;bottom:38px;display:flex;align-items:center;gap:8px}
  .back-brand__square{width:14px;height:14px;background:var(--brand-blue)}
  .back-brand__name{font-weight:500;font-size:15px;color:#ffffff}
</style>
</head>
<body>

<section class="card card--front" aria-label="Business card front">
  <div class="brand">
    <span class="brand__square"></span>
    <span class="brand__name">RWT Fittings Ltd</span>
  </div>

  <div class="divider"></div>

  <div class="person">
    <p class="person__name">MARCO PELTIERI</p>
    <p class="person__title">Owner &amp; Manager</p>
  </div>

  <ul class="contact">
    <li class="contact__item">
      <svg viewBox="0 0 10 10"><path d="M2.2 1l1.6 2-1 1c.6 1.3 1.6 2.3 2.9 2.9l1-1 2 1.6-1 1.5C4.6 8.8 1.2 5.4 1 1.9z" fill="var(--brand-blue)"/></svg>
      1-604-551-8293
    </li>
    <li class="contact__item">
      <svg viewBox="0 0 10 10"><rect x=".8" y="2" width="8.4" height="6" fill="none" stroke="var(--brand-blue)" stroke-width="1"/><path d="M1 2.3l4 3 4-3" fill="none" stroke="var(--brand-blue)" stroke-width="1"/></svg>
      RWTFittings@mailbox-demo.com
    </li>
    <li class="contact__item">
      <svg viewBox="0 0 10 10"><circle cx="5" cy="5" r="4.3" fill="none" stroke="var(--brand-blue)" stroke-width="1"/><ellipse cx="5" cy="5" rx="1.8" ry="4.3" fill="none" stroke="var(--brand-blue)" stroke-width=".8"/><path d="M.8 5h8.4" stroke="var(--brand-blue)" stroke-width=".8"/></svg>
      www.rwtfittings-demo.com
    </li>
  </ul>

  <p class="address">
    <svg viewBox="0 0 11 13"><path d="M5.5 12.5S1 7.6 1 4.8a4.5 4.5 0 0 1 9 0c0 2.8-4.5 7.7-4.5 7.7z" fill="var(--brand-blue)"/><circle cx="5.5" cy="4.8" r="1.6" fill="#fff"/></svg>
    1407-5194 Linden Row Burnaby BC, V5H 2K9
  </p>
</section>

<section class="card card--back" aria-label="Business card back">
  <div class="back-pattern" role="img" aria-label="Repeating tonal pattern of the company emblem on a dark ground"></div>
  <div class="back-brand">
    <span class="back-brand__square"></span>
    <span class="back-brand__name">RWT Fittings Ltd</span>
  </div>
</section>

</body>
</html>
```